Copper Lantern

Need a business card for our restaurant. Restaurant and Bar in the mountains of North Idaho. Rustic looking card

rustic design, wood and metal looking, primarily neutral colors

• Name, address, phone number, website, email address

```html
<!DOCTYPE html>
<html lang="en">
<head>
<meta charset="utf-8">
<title>Copper Lantern – Business Card</title>
<link href="https://fonts.googleapis.com/css2?family=Montserrat:wght@400;500;700&display=swap" rel="stylesheet">
<style>
  :root {
    --backdrop: #2b2b2b;
    --card-dark: #141414;
    --card-light: #ffffff;
    --ink-light: #ffffff;
    --ink-dark: #111111;
    --ink-muted: #333333;
    --rule: #1a1a1a;
  }
  * { margin: 0; padding: 0; box-sizing: border-box; }
  html, body { width: 1200px; height: 875px; overflow: hidden; }
  body {
    background: var(--backdrop);
    font-family: "Montserrat", sans-serif;
    position: relative;
  }
  .card {
    position: absolute;
    top: 288px;
    width: 520px;
    height: 300px;
    border-radius: 22px;
    box-shadow: 0 14px 40px rgba(0,0,0,.45);
  }
  .card--back { left: 50px; background: var(--card-dark); }
  .card--front { left: 630px; background: var(--card-light); }

  .seal {
    position: absolute;
    border-radius: 50%;
    display: flex;
    align-items: center;
    justify-content: center;
    text-align: center;
  }
  .card--back .seal {
    width: 200px; height: 200px;
    left: 160px; top: 50px;
    border: 6px solid var(--ink-light);
  }
  .card--front .seal {
    width: 150px; height: 150px;
    left: 40px; top: 75px;
    border: 4px solid var(--ink-dark);
  }
  .seal__name {
    font-weight: 500;
    letter-spacing: .12em;
    text-transform: uppercase;
    line-height: 1.35;
  }
  .card--back .seal__name { color: var(--ink-light); font-size: 18px; }
  .card--front .seal__name { color: var(--ink-dark); font-size: 14px; }

  .divider {
    position: absolute;
    left: 222px; top: 80px;
    width: 2px; height: 140px;
    background: var(--rule);
  }
  .contact {
    position: absolute;
    left: 246px; top: 70px;
    color: var(--ink-muted);
  }
  .contact__name { font-size: 24px; font-weight: 700; color: var(--ink-dark); line-height: 1.1; }
  .contact__title { font-size: 13px; margin-bottom: 12px; }
  .contact__address { font-size: 14px; line-height: 1.3; margin-bottom: 10px; }
  .contact__list { list-style: none; font-size: 14px; line-height: 1.6; }
  .contact__list li { display: flex; align-items: center; gap: 8px; }
  .contact__list svg { width: 13px; height: 13px; fill: var(--ink-dark); }
</style>
</head>
<body>
  <section class="card card--back" aria-label="Card back">
    <div class="seal"><span class="seal__name">Copper<br>Lantern</span></div>
  </section>

  <section class="card card--front" aria-label="Card front">
    <div class="seal"><span class="seal__name">Copper<br>Lantern</span></div>
    <div class="divider"></div>
    <div class="contact">
      <p class="contact__name">Evan Hale</p>
      <p class="contact__title">Managing Director</p>
      <p class="contact__address">48 Ridge Road,<br>Pine Hollow, USA</p>
      <ul class="contact__list">
        <li><svg viewBox="0 0 16 16"><path d="M3 1h3l1.5 4-2 1.3a9 9 0 0 0 4.2 4.2L11 8.5l4 1.5v3a2 2 0 0 1-2 2A13 13 0 0 1 1 3a2 2 0 0 1 2-2z"/></svg>(08) 4410 2286</li>
        <li><svg viewBox="0 0 16 16"><path d="M1 3h14v10H1z M1 3l7 6 7-6" fill="none" stroke="#111" stroke-width="1.6"/></svg>info@copperlantern.com</li>
        <li><svg viewBox="0 0 16 16"><circle cx="8" cy="8" r="7"/><path d="M1 8h14M8 1c3 3 3 11 0 14M8 1c-3 3-3 11 0 14" fill="none" stroke="#fff" stroke-width="1"/></svg>www.copperlantern.com</li>
      </ul>
    </div>
  </section>
</body>
</html>
```